Business Card Design for Marketing Firm

Looking for business card design for higher end marketing firm. Clean but impressionable/trendy. We are a marketing firm that represents manufacturers in the foodservice equipment and supply industry. Our customers are end users such has hotels, restaurants, country clubs, convention centers and casinos as well as distributors of restaurants supplies and equipment, and manufacturers of foodservice equipment and supplies.
Target Market(s)
Hotels, Restaurants, Supply & Equipment Distributors, Foodservice Manufacturers
Industry/Entity Type
Foodservice/Hospitality
Contact Information for Business Card
Name, Title, Contact Number, Email, Website, Social Media, Address
Requirements
Must have
- Clean & Simple but Serious and Impressionable

```html
<!DOCTYPE html>
<html lang="en">
<head>
<meta charset="utf-8">
<title>Meridian Hospitality Reps – Business Card</title>
<link href="https://fonts.googleapis.com/css2?family=Cinzel:wght@400;700&family=Arimo:wght@400&display=swap" rel="stylesheet">
<style>
  :root {
    --navy: #0a0c78;
    --white: #f7f7f7;
    --grey: #7d7b7e;
    --page: #e9e9ec;
    --ink-light: #ffffff;
  }
  * { box-sizing: border-box; margin: 0; padding: 0; }
  html, body { width: 1200px; height: 768px; overflow: hidden; background: var(--page); }
  .sheet {
    position: relative; width: 1200px; height: 768px;
    display: flex; align-items: center; justify-content: center; gap: 40px;
  }
  .card {
    position: relative; width: 540px; height: 308px; border-radius: 18px; overflow: hidden;
    box-shadow: 0 6px 18px rgba(0,0,0,.18);
  }
  /* back */
  .card-back { background: var(--navy); display: flex; align-items: center; justify-content: center; }
  .back-name {
    font-family: 'Cinzel', serif; font-weight: 400; color: var(--ink-light);
    font-size: 38px; letter-spacing: 3px; text-align: center; line-height: 1.15;
  }
  /* front */
  .card-front { background: var(--white); }
  .front-shape { position: absolute; inset: 0; }
  .social { position: absolute; top: 18px; left: 22px; display: flex; gap: 5px; }
  .social span { width: 15px; height: 15px; border-radius: 50%; background: var(--navy); }
  .brand {
    position: absolute; top: 66px; left: 44px;
    font-family: 'Cinzel', serif; font-weight: 400; color: var(--navy);
    font-size: 21px; letter-spacing: 1px; line-height: 1.2;
  }
  .contact {
    position: absolute; right: 28px; bottom: 18px; text-align: right; color: var(--ink-light);
    font-family: 'Arimo', sans-serif; font-size: 14px; line-height: 1.3;
  }
  .contact .person { font-family: 'Cinzel', serif; font-weight: 700; font-size: 21px; letter-spacing: 1px; line-height: 1; }
  .contact .role { font-size: 15px; margin-bottom: 6px; }
  .contact .address { margin-bottom: 6px; }
  .contact .line { display: flex; align-items: center; justify-content: flex-end; gap: 8px; }
  .contact svg { width: 13px; height: 13px; fill: var(--ink-light); }
</style>
</head>
<body>
<main class="sheet">
  <section class="card card-back">
    <p class="back-name">MERIDIAN</p>
  </section>

  <section class="card card-front">
    <svg class="front-shape" viewBox="0 0 540 308" preserveAspectRatio="none" aria-hidden="true">
      <path class="swoosh-grey" d="M0,140 C8,222 80,230 200,190 C280,140 400,52 540,32 L540,308 L0,308 Z" fill="var(--grey)"/>
      <path class="swoosh-navy" d="M0,160 C8,235 80,245 200,205 C280,150 400,60 540,40 L540,308 L0,308 Z" fill="var(--navy)" stroke="var(--white)" stroke-width="3"/>
    </svg>
    <div class="social" aria-label="Social media"><span></span><span></span><span></span></div>
    <p class="brand">MERIDIAN<br>HOSPITALITY REPS</p>
    <div class="contact">
      <p class="person">DANIEL HAYES</p>
      <p class="role">President</p>
      <p class="address">2170 Lakeview Avenue<br>Cedar Grove, NY 11020</p>
      <p class="line">(555) 0142-7788
        <svg viewBox="0 0 24 24"><path d="M6.6 10.8a15.1 15.1 0 0 0 6.6 6.6l2.2-2.2c.3-.3.7-.4 1-.2 1.1.4 2.3.6 3.6.6.6 0 1 .4 1 1V20c0 .6-.4 1-1 1C10.6 21 3 13.4 3 4c0-.6.4-1 1-1h3.5c.6 0 1 .4 1 1 0 1.3.2 2.5.6 3.6.1.3 0 .7-.2 1z"/></svg></p>
      <p class="line">name@MERIDIAN.com
        <svg viewBox="0 0 24 24"><path d="M2 5h20v14H2z M3.5 6.5 12 13l8.5-6.5" stroke="var(--navy)" stroke-width="1.6"/></svg></p>
      <p class="line">www.MERIDIAN.com
        <svg viewBox="0 0 24 24"><circle cx="12" cy="12" r="10"/><path d="M2 12h20M12 2c3 3 3 17 0 20M12 2c-3 3-3 17 0 20" stroke="var(--navy)" stroke-width="1.4" fill="none"/></svg></p>
    </div>
  </section>
</main>
</body>
</html>
```